Corvel Capital LLC

Need Professional Business cards for New Investment Fund

Target Market(s)

High Quality investors

Industry/Entity Type

Financial

Contact Information for Business Card

Phone Number +1 555 284 6190
Name Lukas Varenko
Title Fund Manager
email lv@FundCorvel.com
Website www.FundCorvel.com

Colors

Designer to choose colors to be used in the design.

Requirements
Must have
• Must have our Logo and all of the above. Must be made so lettering and loge can be raised

```html
<!DOCTYPE html>
<html lang="en">
<head>
<meta charset="utf-8">
<title>Quenvari – Business Card</title>
<link rel="stylesheet" href="https://fonts.googleapis.com/css2?family=Raleway:wght@400;500;600&family=Teko:wght@500&display=swap">
<style>
  :root {
    --backdrop: #1e1e1e;
    --card: #434f41;
    --accent: #55bb45;
    --ink: #ffffff;
  }
  * { margin: 0; padding: 0; box-sizing: border-box; }
  html, body { width: 1200px; height: 900px; overflow: hidden; }
  body {
    background: var(--backdrop);
    font-family: "Raleway", sans-serif;
    color: var(--ink);
    position: relative;
  }
  .card {
    position: absolute;
    left: 250px;
    width: 700px;
    height: 400px;
    background: var(--card);
    overflow: hidden;
  }
  .card--front { top: 40px; }
  .card--back { top: 460px; }

  /* Front */
  .brand {
    position: absolute;
    left: 0; right: 0; top: 170px;
    display: flex;
    justify-content: center;
    align-items: center;
    gap: 16px;
  }
  .brand__mark {
    width: 34px; height: 34px;
    background: var(--accent);
  }
  .brand__name {
    font-weight: 600;
    font-size: 44px;
    letter-spacing: 3px;
    color: var(--ink);
  }
  .front-bar {
    position: absolute;
    bottom: 0;
    left: 220px;
    width: 260px;
    height: 10px;
    background: var(--accent);
  }

  /* Back */
  .edge-tick {
    position: absolute;
    width: 6px;
    height: 70px;
    background: var(--accent);
  }
  .edge-tick--left { left: 0; top: 150px; }
  .edge-tick--right { right: 0; top: 285px; }

  .identity {
    position: absolute;
    right: 370px;
    top: 166px;
    text-align: right;
  }
  .identity__name {
    font-family: "Teko", sans-serif;
    font-weight: 500;
    font-size: 38px;
    line-height: 1;
    text-transform: uppercase;
    letter-spacing: 0.5px;
  }
  .identity__title {
    font-size: 19px;
    font-weight: 400;
    margin-top: 2px;
  }
  .divider {
    position: absolute;
    left: 345px;
    top: 160px;
    width: 2px;
    height: 82px;
    background: var(--accent);
  }
  .contacts {
    position: absolute;
    left: 365px;
    top: 160px;
    list-style: none;
  }
  .contacts li {
    display: flex;
    align-items: center;
    gap: 10px;
    font-size: 19px;
    line-height: 27px;
  }
  .contacts svg {
    width: 15px; height: 15px;
    fill: none;
    stroke: var(--accent);
    stroke-width: 1.6;
  }
</style>
</head>
<body>
  <section class="card card--front">
    <div class="brand">
      <span class="brand__mark"></span>
      <span class="brand__name">QUENVARI</span>
    </div>
    <div class="front-bar"></div>
  </section>

  <section class="card card--back">
    <div class="edge-tick edge-tick--left"></div>
    <div class="edge-tick edge-tick--right"></div>

    <div class="identity">
      <p class="identity__name">Lukas Varenko</p>
      <p class="identity__title">Title Fund Manager</p>
    </div>
    <div class="divider"></div>

    <ul class="contacts">
      <li>
        <svg viewBox="0 0 16 16" aria-hidden="true"><path d="M4 1.5l2.5 3-1.5 1.5c.8 1.8 2.2 3.2 4 4l1.5-1.5 3 2.5-1.5 2.5C7 13 3 9 1.5 3z" fill="var(--accent)" stroke="none"/></svg>
        +1 555 284 6190
      </li>
      <li>
        <svg viewBox="0 0 16 16" aria-hidden="true"><rect x="1.5" y="3.5" width="13" height="9" rx="1"/><path d="M1.5 4l6.5 5 6.5-5"/></svg>
        lv@FundCorvel.com
      </li>
      <li>
        <svg viewBox="0 0 16 16" aria-hidden="true"><circle cx="8" cy="8" r="6.5"/><ellipse cx="8" cy="8" rx="3" ry="6.5"/><path d="M1.5 8h13M2.5 4.8h11M2.5 11.2h11"/></svg>
        www.FundCorvel.com
      </li>
    </ul>
  </section>
</body>
</html>
```